Valdane Companies Business Card Design

We need a new business card for our Private Equity Real Estate Development firm, “Valdane” and our EB-5 regional center “Thornmere Regional Center” on one card. We prefer a design that is simple, elegant, and represents the luxury products we design and build as well as the financial security and stability our successful history has produced. We are an industry leader in our field and 3rd generation family business that has evolved into an institutional quality investment platform. Considered design size is standard business card dimensions (3.5 x 2 inches with an additional 1/8 inch space for design elements or backgrounds that extend beyond the finished size of your piece.

Target Market(s)

• High net worth individuals
• Highly skilled technical workers and physicians in the US seeking investment-based immigration opportunities
• Sophisticated private equity investors
• Intermediary partners include domestic attorneys and investment brokers, as well as international agent networks
• US real estate developers

Industry/Entity Type

Finance

Contact Information for Business Card

(Providing placeholder info for personal information, please design for longer character spaces, longer names and addresses etc..)
• Logo for Valdane
• Logo for Thornmere Regional Center
• Full name: Marcus Valdane
• Job title: CEO
• Email address: mvaldane@valdanecompanies.com
• Cell phone number: +1.555.314.2287
• Office number +1.555.628.4410
• Office address: Larkfield Court 5, 4817 Vista Orilla, San Ramon, CA.
• Website: www.valdanecompanies.com

Font styles to use
Serif
Sans Serif

Colors
ec1f27
ffffff
000000

Requirements
Must have
• • Logo for Valdane
• • Logo for Thornmere Regional Center
• - Use rounded corners
• (See .ai file included for logos)
Nice to have
• • Simple, elegant design
• • Aesthetically compatible with our website design (www.valdanecompanies.com)
• • Color palette including but not limited to white, black, and red (as per logos)
Should not have
• - Not too much red color
• - Do not stack both logos on top of each other

```html
<!DOCTYPE html>
<html lang="en">
<head>
<meta charset="utf-8">
<title>Valdane Companies Business Card</title>
<link href="https://fonts.googleapis.com/css2?family=Cinzel:wght@400;700&family=Cormorant+Garamond:wght@500&display=swap" rel="stylesheet">
<style>
  :root {
    --backdrop: #a7a7a7;
    --card: #1a1a1a;
    --name-ink: #8c8c8c;
    --detail-ink: #7a7a7a;
    --rule: #5e5e5e;
    --brand-red: #b51f3b;
    --brand-grey: #5c5c5c;
  }
  * { margin: 0; padding: 0; box-sizing: border-box; }
  html, body {
    width: 1200px;
    height: 1200px;
    overflow: hidden;
    background: var(--backdrop);
  }
  .canvas {
    position: relative;
    width: 1200px;
    height: 1200px;
  }
  .card {
    position: absolute;
    left: 258px;
    width: 684px;
    height: 390px;
    background: var(--card);
    border-radius: 6px;
  }
  .card--front { top: 173px; }
  .card--back { top: 658px; }

  .person {
    position: absolute;
    left: 79px;
    top: 116px;
    font-family: "Cinzel", serif;
    color: var(--name-ink);
  }
  .person__name {
    font-size: 22px;
    font-weight: 400;
    letter-spacing: 0.5px;
    line-height: 1.1;
  }
  .person__title {
    font-size: 18px;
    line-height: 1.2;
  }
  .divider {
    position: absolute;
    left: 79px;
    top: 194px;
    width: 40px;
    height: 1px;
    background: var(--rule);
  }
  .contact {
    position: absolute;
    left: 79px;
    top: 222px;
    list-style: none;
    font-family: "Cormorant Garamond", serif;
    font-weight: 500;
    font-size: 15.5px;
    line-height: 22px;
    color: var(--detail-ink);
  }
  .center-mark {
    position: absolute;
    left: 440px;
    top: 226px;
    width: 168px;
    text-align: center;
    font-family: "Cinzel", serif;
    font-weight: 700;
    color: var(--brand-red);
  }
  .center-mark__square {
    display: block;
    width: 34px;
    height: 34px;
    margin: 0 auto 10px;
    background: var(--brand-red);
  }
  .center-mark__name {
    font-size: 17px;
    line-height: 1.15;
    letter-spacing: 1px;
  }
  .capital-mark {
    position: absolute;
    left: 0;
    right: 0;
    top: 160px;
    text-align: center;
    font-family: "Cinzel", serif;
    font-weight: 700;
    font-size: 50px;
    letter-spacing: 2px;
    color: var(--brand-grey);
  }
</style>
</head>
<body>
<main class="canvas">
  <section class="card card--front" aria-label="Card front">
    <div class="person">
      <p class="person__name">MARCUS VALDANE</p>
      <p class="person__title">CEO</p>
    </div>
    <div class="divider"></div>
    <ul class="contact">
      <li>Cell: +1.555.314.2287</li>
      <li>Office: +1.555.628.4410</li>
      <li>Mail: mvaldane@valdanecompanies.com</li>
      <li>Web: www.valdanecompanies.com</li>
    </ul>
    <div class="center-mark">
      <span class="center-mark__square"></span>
      <p class="center-mark__name">THORNMERE REGIONAL CENTER</p>
    </div>
  </section>
  <section class="card card--back" aria-label="Card back">
    <p class="capital-mark">VALDANE CAPITAL</p>
  </section>
</main>
</body>
</html>
```